San Francisco Leading Consulting firm - 47Vora Web Design Project

•Create a Web Design
•Uncoded webpage layout design
•2 Pages Design - Homepage + Interior Page

Task Description
Hello, we're looking for a re-design our current website www.47vora-example.com

we have a sample mockup design @

http://47vora.pubtrellis-example.org/

This shows the layout that we like and also a sample of 6 pictures that would change based on where you mouse over..

6 pictures HOME design needs to be included.

SMART
THOUGHTFUL
FLEXIBLE
CREATIVE SERVICES
TECHNICAL SERVICES
PARTNERS

sites we like:

http://www.melvanadvisory-example.com/Home.cfm?id=Home
http://www.plinthworks-example.com/index.html

Our company can be best described as: 100+ employees, cutting-edge, depandable, innovative, strong, smart.

Our Primary focus is: IT Consulting Services and Creative Design services

47Vora LLC is a consulting firm providing creative design, business and technology solutions to both private and public interests.

Established in 1996, 47Vora is a San Francisco based company providing specialists for a range of business needs including:

Creative Design Services
•Print
•Logo Design
•Website Design
•Illustration

and

Business and Technology solutions

•Application Software and Web Development
•Business Process Re-Design (BPR)
•Business/Systems Analysis and Requirement Documentation
•Mentoring and Training
•Network/Hardware Installation Services
•System Design and Architecture
•Vendor Management
•Docuvault Architecture and Implementation

our sample mockup site:

Reason: Due to holiday season, we're not available to work with designers and finilize our design.  

Thank you very much for submitting your design.

We appreciate your time and creativity.   Since, our office is currently closed for holidays, we will be reviewing it in details next week and will make our decision as soon as possible.

It would be great if you could submit any of your changes by Wed next week, so it would be part of our reviews. 

Please see updated wireframe under attachments:  we have some minor updates to our wireframe that we would like you to update your designs, if possible.  

We also encorouge you not to use our standard wireframe and come up with more unique designs.   Everything would be considered when we review your design.

 

Target Market(s)

Creative services and professional services clients, including government agencies

Industry/Entity Type

Business

Requirements
Must have
• Clean, professional look, easy navigation

```html
<!DOCTYPE html>
<html lang="en">
<head>
<meta charset="utf-8">
<title>47Vora – Technology Solutions for the 21st Century</title>
<link rel="stylesheet" href="https://fonts.googleapis.com/css2?family=Open+Sans:wght@400;600;700&family=Arimo:wght@400;700&display=swap">
<style>
:root{
  --header-bg:#eef6fa;
  --nav-bg:#dcecf4;
  --text:#333a3f;
  --muted:#6c7378;
  --link:#2a7fb0;
  --cyan:#3fd5ef;
  --accent:#e8a41c;
  --card-border:#e3e6e8;
  --green-a:#c7c25a;
  --green-b:#6f9e5a;
  --wrench:#8e3b45;
  --hand:#8cb13a;
  --pen:#2b93cf;
}
*{margin:0;padding:0;box-sizing:border-box}
html,body{width:1159px;height:1200px;overflow:hidden}
body{position:relative;background:#fff;font-family:"Open Sans",sans-serif;color:var(--text)}
.abs{position:absolute}
.site-header{left:0;top:0;width:1159px;height:100px;background:var(--header-bg)}
.brand{left:147px;top:40px;display:flex;align-items:center;gap:10px;font-size:26px;font-weight:400;color:#2f3b44;letter-spacing:1px}
.brand-mark{width:16px;height:16px;border-radius:50%;background:var(--pen)}
.tagline{left:333px;top:51px;font-size:12.5px;color:#3a4147}
.contact{left:923px;top:16px;font-size:11.5px;color:var(--muted);line-height:1.3}
.contact .big{font-size:16px;color:var(--link)}
.contact .mail{font-size:12px;color:var(--link)}
.main-nav{left:0;top:100px;width:1159px;height:36px;background:var(--nav-bg)}
.nav-item{top:12px;font-size:11px;font-weight:700;letter-spacing:.6px;color:#2f3a40}
.nav-item .chev{color:var(--accent);margin-left:10px}
.search{left:872px;top:108px;width:149px;height:21px;background:#fff;border:1px solid #d3dde2;font-size:8px;font-style:italic;color:#a8b0b4;padding:5px 8px}
.search svg{position:absolute;right:6px;top:4px}
.welcome-title{left:152px;top:166px;font-size:40px;font-weight:400;color:var(--cyan)}
.welcome-text{left:152px;font-size:12px;color:#333;white-space:nowrap}
.slider-band{left:0;top:300px;width:1159px;height:311px;background:linear-gradient(#e5e8ea,#f4f5f6 60%,#e0e3e5)}
.slide-caption{left:140px;top:300px;width:285px;height:311px;background:linear-gradient(160deg,var(--green-a),#9bb257 55%,var(--green-b))}
.slide-photo{left:427px;top:300px;width:545px;height:311px;background:linear-gradient(100deg,#d8cdb9,#ece4d6 45%,#c9a98a 70%,#9c9a8f)}
.slide-strip{left:972px;top:300px;width:48px;height:311px;background:linear-gradient(#d8ec9c,#7fbe5c)}
.slide-title{left:196px;top:420px;font-size:48px;color:#fff}
.slide-sub{left:196px;top:500px;font-size:22px;line-height:1.35;color:#fff}
.dots{left:155px;top:591px;display:flex;gap:6px}
.dots span{width:7px;height:7px;border-radius:50%;background:rgba(255,255,255,.5)}
.dots span.on{background:#fff}
.lower{left:0;top:611px;width:1159px;height:589px;background:linear-gradient(#e6e8e9,#f7f8f8 25%,#fafbfb)}
.card{top:648px;width:256px;height:147px;background:linear-gradient(#fff,#f4f5f6);border:1px solid var(--card-border);border-radius:9px;box-shadow:0 2px 4px rgba(0,0,0,.06)}
.card-reflect{top:798px;width:256px;height:45px;border-radius:9px;background:linear-gradient(rgba(255,255,255,.7),rgba(255,255,255,0))}
.card svg{position:absolute}
.card-title{position:absolute;font-size:18px;color:#2e3438;line-height:1.2}
.card-title small{display:block;font-size:18px;color:var(--muted)}
.card-more{position:absolute;right:18px;bottom:14px;font-size:11.5px;color:#3a3f43}
.card-more b{color:var(--accent);font-weight:400;margin-left:4px}
.clients{left:144px;top:865px;width:584px;height:86px;background:#fff;border:1px solid #d6dadd;border-radius:8px;font-size:16px;color:#5a6166;padding:30px 15px}
.clients svg{position:absolute;right:10px;top:34px}
.testi-head{left:760px;top:862px;font-size:16px;color:#555c61}
.testi-text{left:760px;top:902px;width:236px;font-size:11px;font-style:italic;color:#7a8186;line-height:1.3}
.testi-by{left:794px;top:936px;width:200px;text-align:right;white-space:nowrap;font-size:9.5px;color:#6a7176}
.quote{font-size:30px;font-weight:700;color:#9fd6ee;line-height:1}
.col-head{top:989px;font-size:13px;font-weight:700;color:#3b4145}
.list{font-size:10.3px;color:var(--link);list-style:none;line-height:1.25}
.list li{margin-bottom:12px}
.list li::before{content:"• "}
.divider{left:412px;top:977px;width:1px;height:161px;background:#dde1e3}
.footer-band{left:96px;top:1155px;width:917px;height:45px;background:#fff;box-shadow:0 -2px 4px rgba(0,0,0,.05)}
.copyright{left:0;top:1172px;width:1159px;text-align:center;font-family:"Arimo",sans-serif;font-size:10.5px;color:#222}
</style>
</head>
<body>
<header class="abs site-header"></header>
<div class="abs brand"><span class="brand-mark"></span>47VORA</div>
<div class="abs tagline">Thechnology Solutions for the 21st Century</div>
<div class="abs contact">Call us at<br><span class="big">800.555.0147</span><br><span style="display:block;margin-top:6px">Email us at</span><span class="mail">info@47vora-example.com</span></div>

<nav class="abs main-nav"></nav>
<div class="abs nav-item" style="left:151px;top:112px">COMPANY<span class="chev">›</span></div>
<div class="abs nav-item" style="left:249px;top:112px">CREATIVE SERVICES<span class="chev">›</span></div>
<div class="abs nav-item" style="left:408px;top:112px">TECHNICAL SERVICES<span class="chev">›</span></div>
<div class="abs nav-item" style="left:584px;top:112px">PARTNERS<span class="chev">›</span></div>
<div class="abs nav-item" style="left:695px;top:112px">CONTACT US</div>
<div class="abs search">SEARCH<svg width="12" height="12" viewBox="0 0 12 12"><circle cx="7" cy="5" r="3.5" fill="none" stroke="#e8a41c" stroke-width="1.4"/><line x1="4.5" y1="7.5" x2="1.5" y2="10.5" stroke="#e8a41c" stroke-width="1.6"/></svg></div>

<h1 class="abs welcome-title">welcome</h1>
<p class="abs welcome-text" style="top:225px">47Vora LLC is a consulting firm providing creative design, business and technology solutions to both private and public interests.</p>
<p class="abs welcome-text" style="top:256px">Our experts possess broad industry knowledge which can help with technical and businessprocess challenges, delivering solutions that are creative and cost effective.</p>

<div class="abs slider-band"></div>
<div class="abs slide-caption"></div>
<div class="abs slide-photo" role="img" aria-label="Photo of two business people shaking hands"></div>
<div class="abs slide-strip"></div>
<svg class="abs" style="left:152px;top:440px" width="16" height="34" viewBox="0 0 16 34"><polyline points="14,2 2,17 14,32" fill="none" stroke="#fff" stroke-width="2"/></svg>
<svg class="abs" style="left:988px;top:440px" width="16" height="34" viewBox="0 0 16 34"><polyline points="2,2 14,17 2,32" fill="none" stroke="#fff" stroke-width="2"/></svg>
<div class="abs slide-title">partners</div>
<div class="abs slide-sub">partner with 47VORA<br>award winning team</div>
<div class="abs dots"><span></span><span></span><span></span><span></span><span></span><span class="on"></span></div>

<div class="abs lower"></div>

<div class="abs card" style="left:145px">
  <svg style="left:22px;top:38px" width="40" height="46" viewBox="0 0 40 46"><polygon points="4,44 38,44 4,10" fill="none" stroke="#2b93cf" stroke-width="4"/><polygon points="11,37 24,37 11,24" fill="#2b93cf"/><line x1="8" y1="34" x2="34" y2="4" stroke="#2b93cf" stroke-width="6"/></svg>
  <div class="card-title" style="left:78px;top:46px">Creative<small>Services</small></div>
  <div class="card-more">Lean More<b>›</b></div>
</div>
<div class="abs card" style="left:449px">
  <svg style="left:18px;top:40px" width="44" height="42" viewBox="0 0 44 42"><path d="M30 4a9 9 0 0 0-9 12L4 33l5 5 17-17a9 9 0 0 0 12-9l-6 4-5-2-1-5z" fill="#8e3b45"/><polygon points="28,26 36,34 32,34 32,42 24,42 24,34 20,34" fill="#8e3b45"/></svg>
  <div class="card-title" style="left:75px;top:44px">Business &amp; Technical<small>Services</small></div>
  <div class="card-more">Lean More<b>›</b></div>
</div>
<div class="abs card" style="left:753px">
  <svg style="left:20px;top:46px" width="52" height="40" viewBox="0 0 52 40"><rect x="2" y="8" width="14" height="18" fill="#8cb13a" transform="rotate(-30 9 17)"/><rect x="36" y="8" width="14" height="18" fill="#8cb13a" transform="rotate(30 43 17)"/><path d="M12 18l12-8 16 12-10 12z" fill="#8cb13a"/></svg>
  <div class="card-title" style="left:90px;top:62px">Partners</div>
  <div class="card-more">Lean More<b>›</b></div>
</div>
<div class="abs card-reflect" style="left:145px"></div>
<div class="abs card-reflect" style="left:449px"></div>
<div class="abs card-reflect" style="left:753px"></div>

<div class="abs clients">Our Clinets<svg width="10" height="16" viewBox="0 0 10 16"><polyline points="2,2 8,8 2,14" fill="none" stroke="#777" stroke-width="2"/></svg></div>
<div class="abs testi-head">Testimonials</div>
<div class="abs quote" style="left:760px;top:884px">“</div>
<p class="abs testi-text">Lorem ipsum dolor sit amet, consectetuer ading elit, sed diam nonummy nibh euismod.</p>
<div class="abs testi-by">Dana Wilde, CEO of Company</div>
<div class="abs quote" style="left:976px;top:954px">”</div>

<h2 class="abs col-head" style="left:146px">Creative Design Services</h2>
<ul class="abs list" style="left:160px;top:1023px">
  <li>Print</li><li>Logo Design</li><li>Website Design</li><li>Illustration</li>
</ul>
<div class="abs divider"></div>
<h2 class="abs col-head" style="left:459px">Business and Technical solutions</h2>
<ul class="abs list" style="left:473px;top:1023px;width:230px">
  <li>Application Software and Web Development</li>
  <li>Business Process Re-Design (BPR)</li>
  <li>Business/Systems Analysis and Requirement<br>&nbsp;&nbsp;Documentation</li>
  <li>Mentoring and Training</li>
</ul>
<ul class="abs list" style="left:732px;top:1023px;width:240px">
  <li>Network/Hardware Installation Services</li>
  <li>System Design and Architecture</li>
  <li>Vendor Management</li>
  <li>Docuvault Architecture and Implementation</li>
</ul>

<footer class="abs footer-band"></footer>
<div class="abs copyright">Copyright 2010, 47Vora, LLC All rights reserved.</div>
</body>
</html>
```